limo company looking for a graphic business card with professional look and feel

Looking for a business card design that can give you the full picture of the limo company by looking at the card - we provide airport service, wedding, birthday, night out, etc... we have sedans, suvs , limos, and party buses. I want the business card to have a professional look because we are targetting corporate clients as well as regular retail.
Info about the business can be found at: http://brevlink.example/Qm4Tz7
Target Market(s)
corporate clients and retail
Industry/Entity Type
Business
Contact Information for Business Card
I would like the logo and the name of the company to be in raised print - not sure if design makes a difference for that or just print - I need it designed in 350dpi
Requirements
Must have
- pictures of vehicle types (sedans, suvs, limos, party bus). pictures of interior of the limos if possible. list service types (weddings, birthdays, proms, airport transportation) & service areas (houston, the woodlands, spring, tomball, cypress, kingwood).
Nice to have
- nice professional look to it.

```html
<!DOCTYPE html>
<html lang="en">
<head>
<meta charset="utf-8">
<title>Grandview Limousine business cards</title>
<link rel="stylesheet" href="https://fonts.googleapis.com/css2?family=Open+Sans:wght@400;600&display=swap">
<style>
  :root {
    --page: #d8d4cf;
    --card: #2c2c2c;
    --card-edge: #1f1f1f;
    --raised: #5c5c5c;
    --ink: #f2f2f2;
    --ink-soft: #d6d6d6;
  }
  * { box-sizing: border-box; margin: 0; padding: 0; }
  html, body { width: 1200px; height: 768px; overflow: hidden; }
  body {
    background: var(--page);
    font-family: "Open Sans", Arial, sans-serif;
    position: relative;
  }
  .card {
    position: absolute;
    top: 229px;
    width: 540px;
    height: 310px;
    background: var(--card);
    border: 1px solid var(--card-edge);
    overflow: hidden;
  }
  .card--front { left: 40px; }
  .card--back { left: 620px; }

  .brand {
    position: absolute;
    top: 24px;
    left: 230px;
    width: 290px;
    text-align: center;
    font-weight: 600;
    line-height: 1.15;
  }
  .brand__name { display: block; font-size: 24px; letter-spacing: 0.5px; }
  .brand__tag { display: block; font-size: 14px; letter-spacing: 1px; }
  .card--front .brand { color: var(--raised); }
  .card--back .brand { color: var(--ink); }

  .collage {
    position: absolute;
    left: 0; top: 86px;
    width: 450px; height: 224px;
    background:
      radial-gradient(ellipse at 25% 80%, rgba(60,60,64,0.85), transparent 60%),
      linear-gradient(110deg, #34405a 0%, #5a3430 30%, #7a5a44 55%, #8c8478 72%, #4e5670 88%, #5c4a30 100%);
    opacity: 0.85;
  }

  .contacts {
    position: absolute;
    left: 26px; top: 96px;
    list-style: none;
    font-size: 13px;
    color: var(--ink-soft);
  }
  .contacts li { display: flex; align-items: center; gap: 12px; height: 20px; }
  .contacts svg { width: 12px; height: 12px; fill: none; stroke: var(--ink-soft); stroke-width: 1.4; }

  .address {
    position: absolute;
    left: 330px; top: 138px;
    font-size: 13px;
    line-height: 1.5;
    color: var(--ink);
    font-style: normal;
  }

  .gallery {
    position: absolute;
    left: 14px; top: 216px;
    display: flex; gap: 8px;
  }
  .gallery__tile { width: 122px; height: 78px; opacity: 0.8; }
  .gallery__tile--green { background: linear-gradient(135deg, #123322, #2f7a48 55%, #10261a); }
  .gallery__tile--blue { background: linear-gradient(135deg, #141b36, #34447e 55%, #151a30); }
  .gallery__tile--navy { background: linear-gradient(135deg, #161e3a, #30447a 55%, #4a4668); }
  .gallery__tile--street { background: linear-gradient(180deg, #7f97b0 0%, #9aa2a8 50%, #3e3e3e 72%, #8a8680 100%); }
</style>
</head>
<body>

  <section class="card card--front" aria-label="Business card front">
    <div class="brand">
      <span class="brand__name">Grandview Limousine</span>
      <span class="brand__tag">&amp; Transportation</span>
    </div>
    <div class="collage" role="img" aria-label="Photo collage of sedans, a white stretch limousine, limo interiors and a wedding couple"></div>
  </section>

  <section class="card card--back" aria-label="Business card back">
    <div class="brand">
      <span class="brand__name">Grandview Limousine</span>
      <span class="brand__tag">&amp; Transportation</span>
    </div>

    <ul class="contacts">
      <li>
        <svg viewBox="0 0 12 12" aria-hidden="true"><path d="M2 1h2.5l1 3-1.5 1a6 6 0 0 0 3 3l1-1.5 3 1V11h-1A9 9 0 0 1 1 2V1z"/></svg>
        713-555-0148
      </li>
      <li>
        <svg viewBox="0 0 12 12" aria-hidden="true"><rect x="1" y="2.5" width="10" height="7"/><path d="M1 2.5l5 4 5-4"/></svg>
        service@grandviewlimoco.example
      </li>
      <li>
        <svg viewBox="0 0 12 12" aria-hidden="true"><circle cx="6" cy="6" r="5"/><path d="M1 6h10M6 1c-2.5 3-2.5 7 0 10M6 1c2.5 3 2.5 7 0 10"/></svg>
        www.grandviewlimoco.example
      </li>
    </ul>

    <address class="address">
      18 Cedar Point 2460 Cedar Point<br>
      Pkwy, Suite #210<br>
      Riverton, TX 77000
    </address>

    <div class="gallery">
      <div class="gallery__tile gallery__tile--green" role="img" aria-label="Party bus interior with green lighting"></div>
      <div class="gallery__tile gallery__tile--blue" role="img" aria-label="Limousine interior with blue lighting"></div>
      <div class="gallery__tile gallery__tile--navy" role="img" aria-label="Party bus lounge seating in blue light"></div>
      <div class="gallery__tile gallery__tile--street" role="img" aria-label="Black party bus parked outside"></div>
    </div>
  </section>

</body>
</html>
```